Ward Compass Business Card Design*

We need a business card design for our company Ward Compass. Our company is specialized in providing online consulting services regarding medical institutions, hospitals and doctors. We work with patients worldwide looking to choose between healthcare providers. We have a website you may use as a reference, where we list doctors and clinics worldwide. So we target Medical providers as well as patients worldwide.
Target Market(s)
Medical Providers and patients around the world
Industry/Entity Type
Medical
Contact Information for Business Card
Salwa Kettani
CEO
+90 612 348 2175
info@wardcompass.example
www.wardcompass.example
14 Annakhil 7 H.R.B. Rabat, Morocco
Requirements
Must have
- Company logo/name on one full side, personal info and smaller logo and company name on the other side.
Nice to have
- Smart and elegant design

```html
<!DOCTYPE html>
<html lang="en">
<head>
<meta charset="utf-8">
<title>Ward Compass – Business Card</title>
<link rel="stylesheet" href="https://fonts.googleapis.com/css2?family=Mulish:wght@400;700&display=swap">
<style>
  :root {
    --navy: #1b4474;
    --grey: #807e80;
    --paper: #f3f3f5;
    --white: #ffffff;
    --stage: #e4e1dc;
    --ink: #3a3a3c;
  }
  * { margin: 0; padding: 0; box-sizing: border-box; }
  html, body { width: 900px; height: 1200px; overflow: hidden; }
  body {
    background: var(--stage);
    font-family: "Mulish", "Helvetica Neue", Arial, sans-serif;
    position: relative;
  }
  .card {
    position: absolute;
    left: 77px;
    width: 746px;
    height: 437px;
  }
  .card--front { top: 134px; background: var(--navy); color: var(--white); }
  .card--back { top: 637px; background: var(--paper); }

  .person { position: absolute; left: 64px; top: 52px; }
  .person__name { font-size: 25px; font-weight: 400; letter-spacing: 0.3px; line-height: 1; }
  .person__name strong { font-weight: 700; }
  .person__role { font-size: 17px; margin-top: 4px; line-height: 1; }

  .contact { position: absolute; left: 64px; top: 338px; list-style: none; }
  .contact__item { display: flex; align-items: center; font-size: 17px; height: 26px; }
  .contact__icon { width: 19px; height: 19px; margin-right: 19px; flex: none; }

  .brand-side {
    position: absolute; right: 60px; top: 110px; width: 230px;
    display: flex; flex-direction: column; align-items: center;
  }
  .brand-side__dot { width: 150px; height: 150px; border-radius: 50%; background: var(--grey); }
  .brand-side__name { margin-top: 20px; font-size: 22px; font-weight: 700; letter-spacing: 1px; color: var(--white); }

  .brand {
    position: absolute; left: 136px; top: 156px;
    display: flex; align-items: center;
  }
  .brand__dot { width: 110px; height: 110px; border-radius: 50%; background: var(--navy); margin-right: 26px; }
  .brand__name { font-size: 44px; font-weight: 700; color: var(--navy); letter-spacing: 0.5px; }

  .website {
    position: absolute; left: 0; right: 0; bottom: 24px;
    text-align: center; font-size: 17px; color: var(--ink);
  }
</style>
</head>
<body>
  <section class="card card--front">
    <div class="person">
      <h1 class="person__name"><strong>SALWA</strong> KETTANI</h1>
      <p class="person__role">CEO</p>
    </div>

    <ul class="contact">
      <li class="contact__item">
        <svg class="contact__icon" viewBox="0 0 20 20" aria-hidden="true">
          <circle cx="10" cy="10" r="10" fill="#fff"/>
          <path d="M6.6 5.2c.4-.3.9-.2 1.1.2l.9 1.6c.2.4.1.8-.2 1.1l-.6.5c.5 1.2 1.4 2.1 2.6 2.6l.5-.6c.3-.3.7-.4 1.1-.2l1.6.9c.4.2.5.7.2 1.1l-.7.9c-.4.5-1.1.7-1.7.5-2.6-.9-4.6-2.9-5.5-5.5-.2-.6 0-1.3.5-1.7z" fill="#1b4474"/>
        </svg>
        +90 612 348 2175
      </li>
      <li class="contact__item">
        <svg class="contact__icon" viewBox="0 0 20 20" aria-hidden="true">
          <circle cx="10" cy="10" r="10" fill="#fff"/>
          <rect x="5.5" y="6.8" width="9" height="6.4" rx="0.6" fill="#1b4474"/>
          <path d="M5.8 7.2 10 10.3l4.2-3.1" fill="none" stroke="#fff" stroke-width="0.9"/>
        </svg>
        info@wardcompass.example
      </li>
    </ul>

    <div class="brand-side">
      <div class="brand-side__dot"></div>
      <p class="brand-side__name">WARD COMPASS</p>
    </div>
  </section>

  <section class="card card--back">
    <div class="brand">
      <div class="brand__dot"></div>
      <p class="brand__name">WARD COMPASS</p>
    </div>
    <p class="website">www.wardcompass.example</p>
  </section>
</body>
</html>
```